Food Hall in San Clemente, CA by the Pacific Ocean that has 15 vendors and 2 bars

We need a web page design that highlights our food hall in San Clemente, CA. The name of the food hall is Calloway Food Hall. Inside of the food hall there are 15 different vendors and 2 bars. The place has a beautiful patio and it is by Pacific Ocean. Most of the vendors are local to San Clemente area. The highly anticipated location is opening during the summer of 2025. Website should have a dropdown menu for the different vendors that are in the food hall and people should be able to click to their respective business website. The website should also include link to our social media channels and also a link to provide comments and subscribe for the mailing list.
Target Market(s)
Mostly residents in the San Clemente, CA and surrounding areas. Couples, families and tourist alike that are looking for an exceptional dining experience that everyone can find something they like.
Industry/Entity Type
Restaurants
Coding
Number of Pages Required
Font styles to use
Look and feel

```html
<!DOCTYPE html>
<html lang="en">
<head>
<meta charset="utf-8">
<title>Calloway Food Hall · San Clemente</title>
<link href="https://fonts.googleapis.com/css2?family=Poppins:wght@400;500;600;700&family=Inter:wght@400;500&display=swap" rel="stylesheet">
<style>
:root{
  --yellow:#fdbd2c;
  --yellow-deep:#f5a800;
  --black:#0b0b0b;
  --dark:#161616;
  --ink:#1a1a1a;
  --muted:#555;
  --white:#fff;
  --line:#d6d6d6;
  --red:#e02424;
}
*{box-sizing:border-box;margin:0;padding:0}
html,body{width:1200px;height:4004px;overflow:hidden}
body{font-family:"Inter",sans-serif;color:var(--ink);background:var(--white);position:relative}
.abs{position:absolute}
h1,h2,h3,.heading{font-family:"Poppins",sans-serif}
.ph{position:absolute;overflow:hidden}

/* header */
.site-header{position:absolute;left:0;top:0;width:1200px;height:85px;background:var(--white)}
.brand{left:112px;top:26px;font:700 27px "Poppins",sans-serif;color:var(--black)}
.nav a{position:absolute;top:33px;font:400 15px "Poppins",sans-serif;color:var(--ink);text-decoration:none}
.nav a.active{color:var(--yellow-deep)}
.btn-login{position:absolute;left:904px;top:24px;width:88px;height:36px;border-radius:18px;background:var(--black);color:var(--white);font:600 16px "Poppins",sans-serif;text-align:center;line-height:36px}
.btn-signup{position:absolute;left:1000px;top:24px;width:90px;height:36px;border-radius:18px;background:var(--yellow);color:var(--white);font:600 16px "Poppins",sans-serif;text-align:center;line-height:36px}

/* hero */
.hero{position:absolute;left:0;top:85px;width:1200px;height:599px;background:var(--yellow)}
.hero h1{position:absolute;left:110px;top:95px;width:520px;font-size:49px;line-height:64px;font-weight:600;color:var(--black)}
.hero p{position:absolute;left:110px;top:232px;width:460px;font-size:14.5px;line-height:27px;font-weight:500}
.search-box{position:absolute;left:110px;top:330px;width:226px;height:44px;background:var(--white);border-radius:3px;font:500 15px "Inter",sans-serif;line-height:44px;padding-left:20px;box-shadow:0 2px 4px rgba(0,0,0,.08)}
.search-box .ic{position:absolute;right:18px;top:8px;width:29px;height:29px;border-radius:50%;background:var(--black)}
.chip{position:absolute;width:178px;height:42px;background:var(--white);border-radius:3px;text-align:center;line-height:42px;font:500 15px "Inter",sans-serif;box-shadow:0 2px 4px rgba(0,0,0,.08)}
.hero-photo{left:634px;top:112px;width:456px;height:385px;border-radius:14px;background:linear-gradient(160deg,#5e6a8c 0%,#2a2c3c 45%,#8a5a2c 75%,#c48a3c 100%)}
.hero-notch{left:905px;top:100px;width:185px;height:97px;background:var(--yellow);border-bottom-left-radius:16px}
.hero-dish{left:913px;top:110px;width:84px;height:84px;border-radius:50%;background:radial-gradient(circle,#7a3a2a,#2f5a22);border:3px solid var(--white)}

.rating-bar{position:absolute;left:0;top:684px;width:1200px;height:56px;background:var(--black)}
.rating-bar .label{position:absolute;left:112px;top:16px;font:600 19px "Poppins",sans-serif;color:var(--yellow)}
.rating-bar .stars{position:absolute;left:978px;top:17px}

/* about */
.about h2{position:absolute;left:111px;top:850px;width:480px;font-size:32px;line-height:47px;font-weight:600}
.dotted{position:absolute;left:112px;top:961px;width:428px;border-top:1.5px dotted #444}
.about p{position:absolute;left:111px;width:460px;font-size:16px;line-height:31px;color:#222}
.about-photo{left:626px;top:848px;width:464px;height:308px;border-radius:60px 20px 60px 20px;background:radial-gradient(ellipse at 50% 50%,#c8842e 0%,#7a9a4a 30%,#e8e2d6 55%,#3c3a36 100%)}

/* vendors */
.section-title{position:absolute;left:0;width:1200px;text-align:center;font:600 40px "Poppins",sans-serif;color:var(--black)}
.vendors-intro{position:absolute;left:160px;top:1320px;width:880px;text-align:center;font-size:16.5px;line-height:31px;color:#333}
.vendor-circle{left:112px;top:1470px;width:223px;height:223px;border-radius:50%;background:radial-gradient(circle,#e8d6a0 0%,#9ab65a 45%,#c9a06a 75%,#7a8aa0 100%)}
.vendor-room{left:766px;top:1462px;width:324px;height:227px;border-radius:40px 14px 40px 14px;background:linear-gradient(180deg,#3a3a3a 0%,#6a6258 45%,#5c7a3a 80%,#3b5a2a 100%)}
.vendor-row{position:absolute;left:368px;width:374px;height:51px;border:1px solid #8a8a8a;border-radius:3px;font-size:16px;color:#888;line-height:49px;padding-left:20px;text-decoration:none;background:var(--white);box-shadow:0 2px 4px rgba(0,0,0,.1)}
.vendor-row svg{position:absolute;right:18px;top:15px}
.view-all{position:absolute;left:522px;top:1743px;font:600 17px "Poppins",sans-serif;text-decoration:underline;color:var(--black)}

/* patio */
.patio{position:absolute;left:0;top:1864px;width:1200px;height:563px;background:linear-gradient(180deg,#151515,#1e1e1e 60%,#121212)}
.patio-sushi{left:138px;top:98px;width:386px;height:310px;border:3px solid var(--yellow);border-radius:14px;background:linear-gradient(135deg,#d8d4c8 0%,#f2efe8 40%,#c29a3a 75%,#2a2a2a 100%)}
.patio-salad{left:314px;top:242px;width:261px;height:220px;border:4px solid var(--white);border-radius:14px;background:radial-gradient(circle,#e08a3a 0%,#7aa040 50%,#1e1e1e 90%)}
.patio h2{position:absolute;left:636px;top:96px;font-size:36px;font-weight:600;color:var(--white)}
.patio .lede{position:absolute;left:636px;top:150px;width:420px;font-size:19px;line-height:30px;font-weight:500;color:var(--white)}
.patio .body{position:absolute;left:636px;top:222px;width:455px;font-size:14px;line-height:27.5px;color:#e8e8e8}
.btn-yellow{position:absolute;width:133px;height:46px;border-radius:23px;background:var(--yellow);color:var(--white);font:600 16px "Poppins",sans-serif;text-align:center;line-height:46px}

/* testimonials */
.card{position:absolute;top:2577px;width:227px;height:311px;background:var(--white);box-shadow:0 2px 8px rgba(0,0,0,.12);text-align:center}
.card .quote{position:absolute;left:0;top:2px;width:100%;font:700 62px/1 "Poppins",sans-serif;color:var(--black)}
.card .stars{position:absolute;left:72px;top:80px}
.card p{position:absolute;left:12px;top:113px;width:203px;font-size:13px;line-height:20.5px;color:#666}
.card .avatar{position:absolute;left:50px;top:222px;width:52px;height:52px;border-radius:50%;background:linear-gradient(160deg,#c8c8c8,#6a5a4e)}
.card .name{position:absolute;left:112px;top:228px;font:600 16px "Poppins",sans-serif;text-align:left}
.card .place{position:absolute;left:112px;top:254px;font-size:12px;color:#777;text-align:left}
.arrow{position:absolute;top:2718px}

/* promo */
.promo{left:112px;top:2986px;width:978px;height:474px;border-radius:40px;background:linear-gradient(90deg,#2e3a2e 0%,#3c4a50 25%,#1e2228 45%,#6a4a2a 65%,#e0a24a 78%,#3a2a1e 100%)}
.poster{position:absolute;left:310px;top:3020px;width:205px;height:320px;background:var(--white);border:5px solid #1d1d1d;text-align:center}
.poster h3{margin-top:36px;font-size:27px;line-height:40px;font-weight:600}
.poster .off{margin-top:8px;font:700 25px "Poppins",sans-serif;color:var(--red)}
.poster p{margin:10px auto 0;width:160px;font-size:14.5px;line-height:26px}
.poster .btn-red{display:inline-block;margin-top:12px;width:138px;height:38px;border-radius:19px;background:var(--red);color:var(--white);font:600 14px/38px "Poppins",sans-serif}

/* footer */
.footer{position:absolute;left:0;top:3560px;width:1200px;height:444px;background:var(--dark);color:var(--white)}
.footer h4{position:absolute;top:68px;font:600 21px "Poppins",sans-serif;text-transform:uppercase}
.quick a{position:absolute;left:124px;font-size:15px;color:var(--white);text-decoration:none}
.quick svg{position:absolute;left:98px}
.social{position:absolute;top:253px;width:30px;height:30px;border-radius:50%;border:1.5px solid var(--white)}
.vline{position:absolute;top:90px;width:0;height:240px;border-left:1px solid #777}
.contact-ic{position:absolute;left:357px;width:30px;height:30px;border-radius:50%;background:var(--yellow)}
.contact-label{position:absolute;left:400px;font:500 17px "Inter",sans-serif}
.contact-val{position:absolute;left:400px;font-size:15px}
.hr-dotted{position:absolute;left:355px;width:240px;border-top:1px dotted #aaa}
.field{position:absolute;left:715px;width:354px;height:40px;border:1.5px solid var(--white);border-radius:20px;font-size:14px;line-height:37px;padding-left:22px}
.submit{position:absolute;left:715px;top:264px;width:354px;height:38px;border-radius:19px;background:var(--yellow);text-align:center;font:600 17px/38px "Poppins",sans-serif}
.foot-rule{position:absolute;left:98px;top:388px;width:1004px;border-top:1px solid #888}
.copyright{position:absolute;left:0;top:410px;width:1200px;text-align:center;font-size:14px}
</style>
</head>
<body>

<header class="site-header">
  <div class="abs brand">Calloway Food Hall</div>
  <nav class="nav">
    <a class="active" href="#" style="left:516px">Home</a>
    <a href="#" style="left:600px">About Us</a>
    <a href="#" style="left:705px">Services</a>
    <a href="#" style="left:806px">Vendors
      <svg width="10" height="8" viewBox="0 0 10 8"><path d="M1 2h8L5 7z" fill="#1a1a1a"/></svg></a>
  </nav>
  <div class="btn-login">Login</div>
  <div class="btn-signup">Sign Up</div>
</header>

<section class="hero">
  <h1>By the Pacific Ocean in San Clemente</h1>
  <p>Opening Summer 2025 — Featuring 15 local vendors and 2 lively bars, a spacious patio, and flavors that reflect the heart of San Clemente.</p>
  <div class="search-box">Find Great Food
    <span class="ic"><svg width="29" height="29" viewBox="0 0 29 29"><circle cx="13" cy="13" r="5" fill="none" stroke="#fff" stroke-width="2"/><path d="M17 17l4 4" stroke="#fff" stroke-width="2"/></svg></span>
  </div>
  <div class="chip" style="left:110px;top:391px">Healthy Food</div>
  <div class="chip" style="left:302px;top:391px">Vitamins</div>
  <div class="chip" style="left:110px;top:449px">Nutritions</div>
  <div class="chip" style="left:302px;top:449px">Supplements</div>
  <div class="ph hero-photo" role="img" aria-label="Food hall storefront lit at dusk"></div>
  <div class="ph hero-notch"></div>
  <div class="ph hero-dish" role="img" aria-label="Colourful salad bowl seen from above"></div>
</section>

<div class="rating-bar">
  <div class="label">3,5000 Rating</div>
  <svg class="stars" width="108" height="22" viewBox="0 0 108 22">
    <defs><path id="st" d="M10 1l2.6 6 6.4.5-4.9 4.2 1.5 6.3L10 14.6 4.4 18l1.5-6.3L1 7.5 7.4 7z"/></defs>
    <use href="#st" x="0" fill="#fdbd2c"/>
    <use href="#st" x="22" fill="#fdbd2c"/>
    <use href="#st" x="44" fill="#fdbd2c"/>
    <use href="#st" x="66" fill="none" stroke="#fdbd2c" stroke-width="1.5"/>
    <use href="#st" x="88" fill="none" stroke="#fdbd2c" stroke-width="1.5"/>
  </svg>
</div>

<section class="about">
  <h2>Enjoy the Authentic Taste of real, flavorful recipes</h2>
  <div class="dotted"></div>
  <p style="top:990px">Calloway Food Hall is more than just dining — it's a curated gathering place that celebrates</p>
  <p style="top:1083px">San Clemente's local flavor, coastal lifestyle, and community spirit.</p>
  <div class="ph about-photo" role="img" aria-label="Granola bowl with berries and avocado"></div>
</section>

<section class="vendors">
  <h2 class="section-title" style="top:1255px">Our Vendors</h2>
  <p class="vendors-intro">Lorem ipsum dolor sit amet, consectetur adipiscing elit, sed do eiusmod tempor incididunt ut labore et dolore magna aliqua. Ut enim ad minim veniam, quis nostrud exercitation ullamco laboris nisi ut aliquip ex ea commodo consequat.</p>
  <div class="ph vendor-circle" role="img" aria-label="Hands holding halved wraps"></div>
  <a class="vendor-row" href="#" style="top:1442px">Tide Taco<svg width="20" height="20" viewBox="0 0 20 20"><circle cx="10" cy="10" r="9" fill="none" stroke="#888"/><path d="M7 13l6-6M8 7h5v5" fill="none" stroke="#888"/></svg></a>
  <a class="vendor-row" href="#" style="top:1516px">Roll Harbor Sushi<svg width="20" height="20" viewBox="0 0 20 20"><circle cx="10" cy="10" r="9" fill="none" stroke="#888"/><path d="M7 13l6-6M8 7h5v5" fill="none" stroke="#888"/></svg></a>
  <a class="vendor-row" href="#" style="top:1590px">Canyon Smoke BBQ<svg width="20" height="20" viewBox="0 0 20 20"><circle cx="10" cy="10" r="9" fill="none" stroke="#888"/><path d="M7 13l6-6M8 7h5v5" fill="none" stroke="#888"/></svg></a>
  <a class="vendor-row" href="#" style="top:1664px">Shoreline Slice<svg width="20" height="20" viewBox="0 0 20 20"><circle cx="10" cy="10" r="9" fill="none" stroke="#888"/><path d="M7 13l6-6M8 7h5v5" fill="none" stroke="#888"/></svg></a>
  <div class="ph vendor-room" role="img" aria-label="Busy food hall dining room"></div>
  <a class="view-all" href="#">View All</a>
</section>

<section class="patio">
  <div class="ph patio-sushi" role="img" aria-label="Sushi rolls with chopsticks"></div>
  <div class="ph patio-salad" role="img" aria-label="Salad bowl with crispy toppings"></div>
  <h2>Chill on the Patio</h2>
  <p class="lede">Enjoy ocean breezes, craft cocktails, and a lively vibe.</p>
  <p class="body">Lorem ipsum dolor sit amet, consectetur adipiscing elit, sed do eiusmod tempor incididunt ut labore et dolore magna aliqua. Ut enim ad minim veniam, quis nostrud exercitation ullamco laboris nisi ut aliquip ex ea commodo consequat. Duis aute irure dolor in reprehenderit in voluptate velit esse cillum dolore eu fugiat nulla pariatur.</p>
  <div class="btn-yellow" style="left:636px;top:409px">Read More</div>
</section>

<section class="testimonials">
  <h2 class="section-title" style="top:2498px">Client Testimonials</h2>
  <svg class="arrow" style="left:42px" width="18" height="32" viewBox="0 0 18 32"><path d="M15 2L3 16l12 14" fill="none" stroke="#222" stroke-width="2"/></svg>
  <svg class="arrow" style="left:1140px" width="18" height="32" viewBox="0 0 18 32"><path d="M3 2l12 14L3 30" fill="none" stroke="#222" stroke-width="2"/></svg>

  <svg width="0" height="0" style="position:absolute"><defs><path id="s5" d="M8 0l2 5 5 .3-4 3.3 1.3 5.1L8 11 3.7 13.7 5 8.6 1 5.3 6 5z"/></defs></svg>

  <div class="card" style="left:112px"><div class="quote">“</div>
    <svg class="stars" width="84" height="15" viewBox="0 0 84 15" fill="#fdbd2c"><use href="#s5"/><use href="#s5" x="17"/><use href="#s5" x="34"/><use href="#s5" x="51"/><use href="#s5" x="68"/></svg>
    <p>Harborline delivers a comprehensive, secure EHR solution designed specifically for South African healthcare providers.</p>
    <div class="avatar" role="img" aria-label="Reviewer portrait"></div><div class="name">Marisol</div><div class="place">United State</div></div>
  <div class="card" style="left:362px"><div class="quote">“</div>
    <svg class="stars" width="84" height="15" viewBox="0 0 84 15" fill="#fdbd2c"><use href="#s5"/><use href="#s5" x="17"/><use href="#s5" x="34"/><use href="#s5" x="51"/><use href="#s5" x="68"/></svg>
    <p>Harborline delivers a comprehensive, secure EHR solution designed specifically for South African healthcare providers.</p>
    <div class="avatar" role="img" aria-label="Reviewer portrait"></div><div class="name">Marisol</div><div class="place">United State</div></div>
  <div class="card" style="left:612px"><div class="quote">“</div>
    <svg class="stars" width="84" height="15" viewBox="0 0 84 15" fill="#fdbd2c"><use href="#s5"/><use href="#s5" x="17"/><use href="#s5" x="34"/><use href="#s5" x="51"/><use href="#s5" x="68"/></svg>
    <p>Harborline delivers a comprehensive, secure EHR solution designed specifically for South African healthcare providers.</p>
    <div class="avatar" role="img" aria-label="Reviewer portrait"></div><div class="name">Marisol</div><div class="place">United State</div></div>
  <div class="card" style="left:862px"><div class="quote">“</div>
    <svg class="stars" width="84" height="15" viewBox="0 0 84 15" fill="#fdbd2c"><use href="#s5"/><use href="#s5" x="17"/><use href="#s5" x="34"/><use href="#s5" x="51"/><use href="#s5" x="68"/></svg>
    <p>Harborline delivers a comprehensive, secure EHR solution designed specifically for South African healthcare providers.</p>
    <div class="avatar" role="img" aria-label="Reviewer portrait"></div><div class="name">Marisol</div><div class="place">United State</div></div>
</section>

<section>
  <div class="ph promo" role="img" aria-label="Cosy café interior with plants and warm window light"></div>
  <div class="poster">
    <h3>Calloway<br>Food Hall</h3>
    <div class="off">30%OFF</div>
    <p>We love food lote of different and fresh food Just like you.</p>
    <span class="btn-red">Start an Order</span>
  </div>
</section>

<footer class="footer">
  <h4 style="left:98px">Quick Links</h4>
  <div class="quick">
    <svg style="top:110px" width="14" height="14" viewBox="0 0 14 14"><path d="M1 7h11M7 2l5 5-5 5" fill="none" stroke="#fff" stroke-width="2"/></svg><a href="#" style="top:107px">Home</a>
    <svg style="top:141px" width="14" height="14" viewBox="0 0 14 14"><path d="M1 7h11M7 2l5 5-5 5" fill="none" stroke="#fff" stroke-width="2"/></svg><a href="#" style="top:138px">About</a>
    <svg style="top:172px" width="14" height="14" viewBox="0 0 14 14"><path d="M1 7h11M7 2l5 5-5 5" fill="none" stroke="#fff" stroke-width="2"/></svg><a href="#" style="top:169px">vendors</a>
    <svg style="top:203px" width="14" height="14" viewBox="0 0 14 14"><path d="M1 7h11M7 2l5 5-5 5" fill="none" stroke="#fff" stroke-width="2"/></svg><a href="#" style="top:200px">Contact</a>
  </div>
  <a class="social" href="#" aria-label="Social channel one" style="left:98px;background:var(--yellow);border-color:var(--yellow)"></a>
  <a class="social" href="#" aria-label="Social channel two" style="left:135px"></a>
  <a class="social" href="#" aria-label="Social channel three" style="left:172px"></a>
  <a class="social" href="#" aria-label="Social channel four" style="left:209px"></a>
  <div class="vline" style="left:302px"></div>

  <h4 style="left:355px">Contact Details</h4>
  <div class="contact-ic" style="top:112px"><svg width="30" height="30" viewBox="0 0 30 30"><path d="M10 9c1-1 2-1 2.5 0l1.3 2.5c.3.6 0 1.2-.5 1.6l-.8.6c.8 1.6 2 2.8 3.6 3.6l.6-.8c.4-.5 1-.8 1.6-.5L20.8 18c1 .5 1 1.5 0 2.5-1.5 1.5-4 1-7-2s-4.3-6-3.8-9.5z" fill="#fff"/></svg></div>
  <div class="contact-label" style="top:106px">Phone:</div>
  <div class="contact-val" style="top:136px">+1 555 014 2200</div>
  <div class="hr-dotted" style="top:171px"></div>
  <div class="contact-ic" style="top:194px"><svg width="30" height="30" viewBox="0 0 30 30"><rect x="8" y="10" width="14" height="10" rx="1" fill="#fff"/><path d="M8 11l7 5 7-5" fill="none" stroke="#fdbd2c" stroke-width="1.4"/></svg></div>
  <div class="contact-label" style="top:188px">Email:</div>
  <div class="contact-val" style="top:218px">hello@callowayhall.example</div>
  <div class="hr-dotted" style="top:252px"></div>
  <div class="contact-ic" style="top:286px"><svg width="30" height="30" viewBox="0 0 30 30"><path d="M15 8a5 5 0 0 1 5 5c0 4-5 9-5 9s-5-5-5-9a5 5 0 0 1 5-5z" fill="#fff"/><circle cx="15" cy="13" r="1.8" fill="#fdbd2c"/></svg></div>
  <div class="contact-label" style="top:280px">Address:</div>
  <div class="contact-val" style="top:311px">Company Name,United State.</div>
  <div class="vline" style="left:670px"></div>

  <h4 style="left:715px">Contact Me</h4>
  <div class="field" style="top:104px">Name:</div>
  <div class="field" style="top:157px">Email:</div>
  <div class="field" style="top:210px">Address:</div>
  <div class="submit">Submit Now</div>

  <div class="foot-rule"></div>
  <div class="copyright">Copyrights@2025.Company Name.All Rights Reserved</div>
</footer>

</body>
</html>
```